Calder Vane LED - E- Commerce site

We need a website designed for an LED Billboard company that sells:
1) LED Billboards (Sales & Rental)
2) LED Gas Station lights
3) Truss Systems (Sales & Rental)
4) Sound Systems (Sales & Rental)

Attached are websites that sell similar products as Calder Vane LED. Target market is for business, property managers and event coordinators.
This site will need to be an e-commerce site where customers can purchase the product directly from the site. What I'm looking for is a design layout to start.

Conceptual Web Designs:
http://192.0.2.47:8087/index.html
http://www.pmvdisplay.example/
http://www.auralomaaudio.example/
http://www.quillmarkpanel.example/

Attached is the logo of the company: Please note that the new spelling of the logo is "Calder Vane LED" using domain " CalderVaneLED.com

Industry/Entity Type

Gas Station

Number of Pages Required

5+ page

Requirements
Must have
• 1) E-Commerce - Customers will need to be able to order product from the site.
• 2) Customers will also have the option to rent the product as well.
Nice to have
• I like the image of the attached website, that has a video clip loop
• http://www.quillmarkpanel.example/

```html
<!DOCTYPE html>
<html lang="en">
<head>
<meta charset="utf-8">
<title>Calder Vane LED</title>
<link href="https://fonts.googleapis.com/css2?family=Baloo+2:wght@600&family=Questrial&family=Open+Sans:wght@400;600&display=swap" rel="stylesheet">
<style>
:root{
  --red:#e3262b;
  --black:#0d0d0d;
  --yellow:#f5c518;
  --glow:#f2d23a;
  --page:#f2f2f2;
  --ink:#1a1a1a;
  --muted:#555;
  --line:#d4d4d4;
  --white:#fff;
}
*{box-sizing:border-box;margin:0;padding:0}
html,body{width:1200px;height:3046px;overflow:hidden}
body{position:relative;background:var(--page);font-family:"Open Sans",Arial,sans-serif;color:var(--ink)}
.abs{position:absolute}

/* header */
.topbar{left:0;top:0;width:1200px;height:93px;background:var(--black)}
.navbar{left:0;top:93px;width:1200px;height:49px;background:var(--red)}
.brand{left:78px;top:16px;display:flex;align-items:center;gap:10px;z-index:2}
.brand-dot{width:40px;height:40px;border-radius:50%;background:var(--red)}
.brand-name{font-family:"Baloo 2",sans-serif;font-weight:600;font-size:25px;line-height:1;color:var(--white);width:120px}
.toplinks{top:12px;font-size:12.5px;color:#e6e6e6;display:flex;align-items:center;gap:6px}
.toplinks svg{width:15px;height:15px}
.search{left:924px;top:53px;width:195px;height:28px;background:var(--white);border-radius:2px;font-size:12px;color:#666;padding:5px 8px}
.search svg{position:absolute;right:6px;top:6px;width:16px;height:16px}
.nav a{position:absolute;top:104px;font-size:16px;color:var(--white);text-decoration:none}
.nav a.current{color:var(--yellow);font-weight:600}

/* hero */
.hero{left:0;top:142px;width:1200px;height:563px;
  background:
    radial-gradient(ellipse 220px 260px at 110px 260px,rgba(80,150,220,.75),transparent 70%),
    radial-gradient(ellipse 160px 200px at 250px 330px,rgba(230,170,160,.55),transparent 70%),
    radial-gradient(ellipse 140px 120px at 480px 420px,rgba(240,200,90,.45),transparent 70%),
    radial-gradient(ellipse 120px 180px at 520px 200px,rgba(200,60,140,.45),transparent 70%),
    radial-gradient(ellipse 130px 90px at 700px 500px,rgba(90,200,120,.4),transparent 70%),
    radial-gradient(ellipse 200px 160px at 380px 120px,rgba(120,110,200,.5),transparent 70%),
    linear-gradient(90deg,#1e2a44 0%,#241c30 40%,#15121a 65%,#0c0a0e 100%)}
.hero-shade{left:600px;top:142px;width:600px;height:563px;background:linear-gradient(90deg,rgba(0,0,0,0),rgba(0,0,0,.45))}
.hero-title{left:630px;top:342px;width:420px;text-align:center;font-family:"Baloo 2",sans-serif;font-weight:600;font-size:42px;line-height:54px;color:var(--glow);text-shadow:0 0 10px rgba(242,210,58,.6)}
.hero-btn{left:778px;top:479px;width:124px;height:43px;background:var(--red);color:var(--white);font-size:16px;font-weight:600;text-align:center;line-height:43px;letter-spacing:.5px}
.hero-notch{left:582px;top:705px;width:0;height:0;border-left:18px solid transparent;border-right:18px solid transparent;border-top:16px solid #2a2a2a}

/* welcome */
.welcome h1{position:absolute;left:0;top:768px;width:1200px;text-align:center;font-family:"Questrial",sans-serif;font-weight:400;font-size:38px;color:var(--ink)}
.rule{height:3px;width:70px;background:linear-gradient(90deg,var(--red) 50%,#222 50%)}
.welcome p{position:absolute;left:118px;top:856px;width:964px;text-align:center;font-size:13.5px;line-height:28px;color:#333}
.welcome p a{color:var(--red);font-weight:600}

/* categories */
.tile{position:absolute;overflow:hidden}
.tile .frame{position:absolute;inset:12px;border:1.5px solid rgba(255,255,255,.85)}
.tile .label{position:absolute;left:0;width:100%;text-align:center;font-family:"Baloo 2",sans-serif;font-weight:600;font-size:31px;color:var(--glow);text-shadow:0 0 8px rgba(242,210,58,.55)}
.tile svg.icon{position:absolute;left:50%;transform:translateX(-50%)}

/* products */
.section-title{left:79px;top:1638px;font-family:"Questrial",sans-serif;font-size:36px;color:var(--ink)}
.card{position:absolute;width:248px;height:211px;background:var(--white);border:1px solid #ddd;border-radius:8px;overflow:hidden}
.card .shot{position:absolute;left:8px;top:8px;width:230px;height:193px}
.product-name{position:absolute;font-size:16px;font-weight:600;color:var(--ink)}
.btn{position:absolute;height:29px;font-size:14px;line-height:29px;text-align:center;width:90px}
.btn.buy{background:var(--red);color:var(--white)}
.btn.rent{background:var(--yellow);color:var(--ink)}
.pager{left:566px;top:2450px;display:flex;gap:14px}

/* service strip */
.strip{left:0;top:2517px;width:1200px;height:181px;background:var(--white)}
.service{position:absolute;top:2562px;width:248px;height:81px;border:1.5px solid #9a9a9a;border-radius:8px;background:var(--white)}
.service .ic{position:absolute;left:14px;top:12px;width:56px;height:56px;border-radius:50%;background:#e5e5e5}
.service .ic.hot{background:var(--yellow)}
.service b{position:absolute;left:100px;top:14px;font-family:"Questrial",sans-serif;font-size:20px;font-weight:400;color:var(--ink)}
.service span{position:absolute;left:100px;top:44px;font-size:11.5px;letter-spacing:.5px;color:#777}

/* footer */
.footer{left:0;top:2698px;width:1200px;height:294px;background:var(--black)}
.fcol{position:absolute;top:2744px}
.fcol h4{font-weight:400;font-size:15px;color:var(--red);margin-bottom:10px}
.fcol li{list-style:none;font-size:12.5px;color:#e6e6e6;line-height:29.5px;padding-left:14px;position:relative}
.fcol li::before{content:"";position:absolute;left:2px;top:12px;border-left:5px solid #ccc;border-top:3.5px solid transparent;border-bottom:3.5px solid transparent}
.fsep{position:absolute;top:2750px;width:1px;height:200px;background:#333}
.contact-row{display:flex;gap:12px;font-size:12.5px;color:#e6e6e6;line-height:20px;margin-bottom:16px}
.contact-row svg{flex:none;width:16px;height:16px;margin-top:2px}
.fbrand{left:950px;top:2752px;display:flex;align-items:center;gap:8px}
.fbrand .brand-dot{width:30px;height:30px}
.fbrand .brand-name{width:96px;font-size:20px}
.accept{left:970px;top:2855px;font-size:16px;color:var(--red)}
.paycard{position:absolute;top:2900px;width:42px;height:28px;border-radius:3px;background:#e9e9e9}
.copybar{left:0;top:2992px;width:1200px;height:54px;background:var(--red);color:var(--white);font-size:13px;text-align:center;line-height:54px}
</style>
</head>
<body>

<!-- header -->
<div class="abs topbar"></div>
<div class="abs navbar"></div>
<div class="abs brand"><span class="brand-dot"></span><span class="brand-name">Calder Vane LED</span></div>

<div class="abs toplinks" style="left:605px">Checkout</div>
<div class="abs toplinks" style="left:700px">My Wishlist</div>
<div class="abs toplinks" style="left:800px">
  <svg viewBox="0 0 16 16" fill="none" stroke="#ddd" stroke-width="1.5"><path d="M9 2h5v12H9M2 8h8M7 5l3 3-3 3"/></svg>Log In</div>
<div class="abs toplinks" style="left:895px">
  <svg viewBox="0 0 16 16" fill="#ddd"><circle cx="8" cy="5" r="3"/><path d="M2 15c0-4 3-6 6-6s6 2 6 6z"/></svg>My Account</div>
<div class="abs toplinks" style="left:1022px">
  <svg viewBox="0 0 16 16" fill="none" stroke="#ddd" stroke-width="1.5"><path d="M1 2h3l2 8h8l1.5-6H5"/><circle cx="7" cy="13" r="1.3" fill="#ddd"/><circle cx="13" cy="13" r="1.3" fill="#ddd"/></svg>My Cart (0)</div>
<div class="abs search">Search
  <svg viewBox="0 0 16 16" fill="none" stroke="#e3262b" stroke-width="2"><circle cx="7" cy="7" r="4.5"/><path d="M10.5 10.5 14 14"/></svg></div>

<nav class="nav">
  <a class="current" style="left:227px">Home</a>
  <a style="left:311px">About Us</a>
  <a style="left:414px">LED Billboard</a>
  <a style="left:548px">LED Gas Station Lights</a>
  <a style="left:751px">Truss Systems</a>
  <a style="left:883px">Sound Systems</a>
  <a style="left:1033px">Contact Us</a>
</nav>

<!-- hero -->
<div class="abs hero" role="img" aria-label="Night city square lit by large LED billboards"></div>
<div class="abs hero-shade"></div>
<div class="abs hero-title">Light Up Your<br>Advertisement</div>
<div class="abs hero-btn">BUY NOW</div>
<div class="abs hero-notch"></div>

<!-- welcome -->
<section class="welcome">
  <h1>Welcome To Calder Vane LED</h1>
  <div class="abs rule" style="left:565px;top:834px"></div>
  <p>Lorem ipsum dolor sit amet, consectetuer adipiscing elit, sed diam nonummy nibh euismod tincidunt ut laoreet dolore magna aliquam erat volutpat. Ut wisi enim ad minim veniam, quis nostrud exerci tation ullamcorper suscipit lobortis nisl ut aliquip ex ea commodo consequat. Duis autem vel eum iriure dolor in hendrerit in vulputate velit esse molestie consequat, ulla facilisi <a>Read More</a></p>
</section>

<!-- categories -->
<div class="tile" style="left:81px;top:1009px;width:483px;height:337px;background:radial-gradient(ellipse 140px 110px at 90px 90px,rgba(70,140,200,.55),transparent 70%),radial-gradient(ellipse 150px 100px at 400px 120px,rgba(200,90,150,.4),transparent 70%),radial-gradient(ellipse 220px 80px at 240px 300px,rgba(60,90,180,.45),transparent 70%),linear-gradient(160deg,#2c3448,#101522 60%,#1b2030)" role="img" aria-label="City street at night with illuminated billboards">
  <div class="frame"></div>
  <svg class="icon" style="top:100px" width="44" height="50" viewBox="0 0 44 50" fill="none" stroke="#fff" stroke-width="2.5"><rect x="4" y="4" width="36" height="24"/><path d="M22 28v14M12 46h20M14 36h16"/></svg>
  <div class="label" style="top:170px">LED Billboards</div>
</div>
<div class="tile" style="left:581px;top:1009px;width:538px;height:221px;background:radial-gradient(ellipse 260px 40px at 270px 30px,rgba(230,230,240,.35),transparent 70%),linear-gradient(180deg,#2a2a2e,#121214 55%,#3a3a3c)" role="img" aria-label="Gas station canopy lit by LED lights">
  <div class="frame"></div>
  <svg class="icon" style="top:52px" width="72" height="40" viewBox="0 0 72 40"><rect x="2" y="2" width="68" height="36" rx="18" fill="#fff"/><g fill="#222"><circle cx="20" cy="14" r="3.5"/><circle cx="31" cy="14" r="3.5"/><circle cx="42" cy="14" r="3.5"/><circle cx="53" cy="14" r="3.5"/><circle cx="20" cy="26" r="3.5"/><circle cx="31" cy="26" r="3.5"/><circle cx="42" cy="26" r="3.5"/><circle cx="53" cy="26" r="3.5"/></g></svg>
  <div class="label" style="top:115px">LED Gas Station Lights</div>
</div>
<div class="tile" style="left:81px;top:1372px;width:483px;height:220px;background:radial-gradient(ellipse at 50% 40%,#23307a,#0b1040 75%)" role="img" aria-label="Truss rig on a blue-lit stage">
  <div class="frame"></div>
  <svg class="icon" style="top:62px" width="110" height="36" viewBox="0 0 110 36" fill="none" stroke="#fff" stroke-width="3"><path d="M4 32 18 6h74l14 26M18 6l12 20L44 6l12 20L70 6l12 20L92 6M30 26h52"/></svg>
  <div class="label" style="top:110px">Truss Systems</div>
</div>
<div class="tile" style="left:581px;top:1252px;width:538px;height:340px;background:radial-gradient(ellipse 60px 120px at 90px 170px,rgba(80,180,200,.35),transparent 70%),radial-gradient(ellipse 60px 120px at 210px 170px,rgba(70,190,100,.35),transparent 70%),radial-gradient(ellipse 60px 120px at 330px 170px,rgba(160,120,220,.4),transparent 70%),radial-gradient(ellipse 60px 120px at 450px 170px,rgba(220,110,150,.35),transparent 70%),linear-gradient(180deg,#606060,#3d3d3d 50%,#2a2a2a)" role="img" aria-label="Row of glowing LED speakers">
  <div class="frame"></div>
  <svg class="icon" style="top:95px" width="74" height="86" viewBox="0 0 74 86" fill="none" stroke="#fff" stroke-width="2"><rect x="38" y="4" width="32" height="78" fill="#fff"/><circle cx="54" cy="22" r="7" fill="#333"/><circle cx="54" cy="54" r="11" fill="#333"/><rect x="4" y="36" width="30" height="46" fill="#fff"/><circle cx="19" cy="50" r="5" fill="#333"/><circle cx="19" cy="69" r="8" fill="#333"/></svg>
  <div class="label" style="top:190px">Sound Systems</div>
</div>

<!-- featured products -->
<h2 class="abs section-title" style="font-weight:400">Featured Product</h2>
<div class="abs rule" style="left:79px;top:1703px"></div>

<div class="card" style="left:81px;top:1746px"><div class="shot" style="background:radial-gradient(ellipse 90px 60px at 100px 80px,#111 0%,#222 55%,rgba(255,255,255,0) 100%),radial-gradient(ellipse 60px 70px at 170px 100px,#bcbcbc,rgba(255,255,255,0) 100%),#fff" role="img" aria-label="Outdoor LED billboard on a pole"></div></div>
<div class="card" style="left:345px;top:1746px"><div class="shot" style="background:radial-gradient(ellipse 100px 70px at 50% 50%,#b8b8b8 0%,#d6d6d6 50%,rgba(255,255,255,0) 100%),#fff" role="img" aria-label="Recessed LED canopy light"></div></div>
<div class="card" style="left:607px;top:1746px"><div class="shot" style="background:radial-gradient(ellipse 80px 75px at 50% 55%,#8d97a8 0%,#c7c7c7 55%,rgba(255,255,255,0) 100%),#fff" role="img" aria-label="LED gas station light fixture"></div></div>
<div class="card" style="left:871px;top:1746px"><div class="shot" style="background:radial-gradient(ellipse 100px 75px at 50% 50%,#9a9a9a 0%,#cfcfcf 50%,rgba(255,255,255,0) 100%),#fff" role="img" aria-label="Aluminium truss frame"></div></div>

<div class="product-name" style="left:81px;top:1974px">LED Billboards</div>
<div class="product-name" style="left:345px;top:1974px">LED Gas Station lights</div>
<div class="product-name" style="left:607px;top:1974px">LED Gas Station lights</div>
<div class="product-name" style="left:871px;top:1974px">Truss Systems</div>

<div class="btn buy" style="left:81px;top:2015px">Buy Now</div><div class="btn rent" style="left:177px;top:2015px">On Rent</div>
<div class="btn buy" style="left:345px;top:2015px">Buy Now</div><div class="btn rent" style="left:441px;top:2015px">On Rent</div>
<div class="btn buy" style="left:607px;top:2015px">Buy Now</div><div class="btn rent" style="left:703px;top:2015px">On Rent</div>
<div class="btn buy" style="left:871px;top:2015px">Buy Now</div><div class="btn rent" style="left:967px;top:2015px">On Rent</div>

<div class="card" style="left:81px;top:2107px"><div class="shot" style="background:radial-gradient(ellipse 52px 62px at 50% 50%,#6a4fb0 0%,#2a2438 60%,rgba(255,255,255,0) 100%),#fff" role="img" aria-label="Cylindrical LED sound speaker"></div></div>
<div class="card" style="left:345px;top:2107px"><div class="shot" style="background:radial-gradient(ellipse 95px 38px at 50% 52%,#d4553a 0%,#4a9a5a 45%,#3c8ec8 75%,rgba(255,255,255,0) 100%),#fff" role="img" aria-label="Portable LED speaker"></div></div>
<div class="card" style="left:607px;top:2107px"><div class="shot" style="background:radial-gradient(ellipse 95px 80px at 50% 50%,#a8a8a8 0%,#d4d4d4 50%,rgba(255,255,255,0) 100%),#fff" role="img" aria-label="Circular truss structure"></div></div>
<div class="card" style="left:871px;top:2107px"><div class="shot" style="background:radial-gradient(ellipse 90px 72px at 50% 50%,#111 0%,#1c1c1c 65%,rgba(255,255,255,0) 100%),#fff" role="img" aria-label="LED display panel"></div></div>

<div class="product-name" style="left:81px;top:2335px">LED Sound Systems</div>
<div class="product-name" style="left:345px;top:2335px">LED Sound Systems</div>
<div class="product-name" style="left:607px;top:2335px">Truss Systems</div>
<div class="product-name" style="left:871px;top:2335px">LED Billboards</div>

<div class="btn buy" style="left:81px;top:2376px">Buy Now</div><div class="btn rent" style="left:177px;top:2376px">On Rent</div>
<div class="btn buy" style="left:345px;top:2376px">Buy Now</div><div class="btn rent" style="left:441px;top:2376px">On Rent</div>
<div class="btn buy" style="left:607px;top:2376px">Buy Now</div><div class="btn rent" style="left:703px;top:2376px">On Rent</div>
<div class="btn buy" style="left:871px;top:2376px">Buy Now</div><div class="btn rent" style="left:967px;top:2376px">On Rent</div>

<div class="abs pager">
  <svg width="28" height="24" viewBox="0 0 28 24" fill="none" stroke="#666" stroke-width="3"><path d="M26 12H4M12 3 3 12l9 9"/></svg>
  <svg width="28" height="24" viewBox="0 0 28 24" fill="none" stroke="#111" stroke-width="3"><path d="M2 12h22M16 3l9 9-9 9"/></svg>
</div>

<!-- services -->
<div class="abs strip"></div>
<div class="service" style="left:81px">
  <div class="ic hot"><svg width="56" height="56" viewBox="0 0 56 56"><path d="M14 22h18v14H14zM32 26h6l4 5v5H32z" fill="#222"/><circle cx="19" cy="37" r="3" fill="#222"/><circle cx="37" cy="37" r="3" fill="#222"/></svg></div>
  <b>Delivery</b><span>INFORMATION</span></div>
<div class="service" style="left:345px">
  <div class="ic"><svg width="56" height="56" viewBox="0 0 56 56" fill="none" stroke="#222" stroke-width="2.5"><path d="M14 18h5l4 15h14l3-11H21"/><circle cx="25" cy="38" r="2" fill="#222"/><circle cx="35" cy="38" r="2" fill="#222"/></svg></div>
  <b>Returns</b><span>QUERY?</span></div>
<div class="service" style="left:607px">
  <div class="ic"><svg width="56" height="56" viewBox="0 0 56 56"><path d="M28 14c-9 0-15 5-15 12 0 4 2 7 5 9l-2 6 7-4c2 .5 3 .5 5 .5 9 0 15-5 15-11.5S37 14 28 14z" fill="#222"/><text x="28" y="32" font-size="14" font-weight="700" fill="#fff" text-anchor="middle" font-family="Open Sans,sans-serif">?</text></svg></div>
  <b>Questions?</b><span>View FAQ's</span></div>
<div class="service" style="left:871px">
  <div class="ic"><svg width="56" height="56" viewBox="0 0 56 56"><path d="M19 15l6 1 2 7-4 3c2 4 5 7 9 9l3-4 7 2 1 6c-2 3-5 3-8 2-8-3-14-9-17-17-1-3-1-6 1-9z" fill="#222"/></svg></div>
  <b>Let Us Help</b><span>CONTACT US</span></div>

<!-- footer -->
<footer class="abs footer"></footer>
<div class="fcol" style="left:81px"><h4>Shop Now</h4><ul><li>Home</li><li>About Us</li><li>LED Billboard</li><li>LED Gas Station Lights</li><li>Truss Systems</li><li>Sound Systems</li><li>Contact Us</li></ul></div>
<div class="fsep" style="left:266px"></div>
<div class="fcol" style="left:300px"><h4>Contact Details</h4>
  <div class="contact-row"><svg viewBox="0 0 16 16"><path d="M8 1a5 5 0 0 0-5 5c0 4 5 9 5 9s5-5 5-9a5 5 0 0 0-5-5zm0 7a2 2 0 1 1 0-4 2 2 0 0 1 0 4z" fill="#e3262b"/></svg><span>Lorem ipsum, Dollar smit,<br>City Code - 1234567.</span></div>
  <div class="contact-row"><svg viewBox="0 0 16 16"><path d="M3 1l3 .5 1 3.5-2 1.5c1 2 2.5 3.5 4.5 4.5L11 9l3.5 1 .5 3c-1 1.5-2.5 1.5-4 1C7 12.5 3.5 9 2 5c-.5-1.5-.5-3 1-4z" fill="#e3262b"/></svg><span>123-456-7890</span></div>
  <div class="contact-row"><svg viewBox="0 0 16 16" fill="none" stroke="#e3262b" stroke-width="1.6"><rect x="1.5" y="3.5" width="13" height="9"/><path d="M1.5 3.5 8 9l6.5-5.5"/></svg><span>info@caldervaneled.com</span></div>
</div>
<div class="fsep" style="left:514px"></div>
<div class="fcol" style="left:546px"><h4>Shopping Online</h4><ul><li>Delivery Information</li><li>Privacy Policy</li><li>Returns Policy</li><li>Terms and Conditions</li><li>FAQs</li></ul></div>
<div class="fsep" style="left:733px"></div>
<div class="fcol" style="left:759px"><h4>About Us</h4><ul><li>About Us</li><li>Careers</li><li>Pet Blog</li><li>Contact Us</li></ul></div>

<div class="abs fbrand"><span class="brand-dot"></span><span class="brand-name">Calder Vane LED</span></div>
<div class="abs accept">We Accept</div>
<div class="paycard" style="left:906px"></div>
<div class="paycard" style="left:960px"></div>
<div class="paycard" style="left:1014px"></div>
<div class="paycard" style="left:1068px"></div>

<div class="abs copybar">Copyright © 2016 Calder Vane LED. All Rights Reserved.</div>

</body>
</html>
```